Preisliste für Kosmetikinstitut
Zielgruppe
Ich benötige für mein Kosmetikinstitut eine Preisliste für die moderne Frau, aber auch Männer. Das Design sollte mein Logo enthalten. Farben des Designkonzepts einbauen.
A4 quer zum Falten, wie ein Heft, 1. Seite Preisliste mit logo, im Innenteil dann Anwendungen
Aufgabenstellung
Minimalistisch, ästhetisch, modern, edel
Kontaktdaten auf der Rückseite
LB Hautatelier
Lotte Brenner
Lindenhang 17
83671 Waakirchen
EMail: lotte@lb-hautatelier.de
Whatsapp: 0176 284 9017

```html
<!DOCTYPE html>
<html lang="de">
<head>
<meta charset="utf-8">
<title>Preisliste – Behandlungen</title>
<link href="https://fonts.googleapis.com/css2?family=Inter:wght@300;400&display=swap" rel="stylesheet">
<style>
:root{
  --canvas:#ffffff;
  --paper:#fbfbf3;
  --ink:#6a706e;
  --ink-soft:#7a807e;
  --shadow:rgba(0,0,0,.28);
  --ornament-light:#ecedea;
  --ornament-mid:#dfe1de;
}
*{margin:0;padding:0;box-sizing:border-box}
html,body{width:1200px;height:1200px;overflow:hidden;background:var(--canvas)}
body{font-family:"Inter",Arial,sans-serif;color:var(--ink);font-weight:300}
.spread{position:absolute;left:39px;top:189px;width:1091px;height:771px;background:var(--paper);box-shadow:1px 3px 4px var(--shadow)}
.page-title{position:absolute;top:41px;font-size:27px;font-weight:300;letter-spacing:-.9px;color:var(--ink);white-space:nowrap}
.page-title.left{left:33px}
.page-title.right{right:50px}
.item{position:absolute;width:371px}
.col-left .item{left:44px}
.col-right .item{left:681px}
.item h3{font-size:12.9px;font-weight:300;letter-spacing:-.3px;line-height:1.2;color:var(--ink);white-space:nowrap}
.item p,.item li{font-size:8.5px;line-height:11px;letter-spacing:-.25px;color:var(--ink-soft);hyphens:auto;-webkit-hyphens:auto}
.item p.gap{margin-top:5px}
.steps{list-style:none;margin-top:10px}
.steps li{padding-left:8px;text-indent:-8px}
.price{display:flex;justify-content:flex-end;gap:20px;font-size:10.2px;margin-top:3px;letter-spacing:-.2px}
.rates{margin-top:14px}
.rates.tight .row{line-height:13.4px}
.row{display:flex;justify-content:space-between;font-size:10.2px;line-height:16.5px;letter-spacing:-.2px;padding-right:6px}
.ornament{position:absolute;left:473px;top:122px;width:151px;height:539px;background:linear-gradient(180deg,var(--ornament-light) 0%,var(--ornament-mid) 50%,var(--ornament-light) 100%)}
</style>
</head>
<body>
<main class="spread">
  <h1 class="page-title left">Gesichtsbehandlungen</h1>
  <h1 class="page-title right">Apparative Behandlungen</h1>

  <section class="col-left">
    <article class="item" style="top:126px">
      <h3>Express Facial Treatment</h3>
      <p>Für alle, die wenig Zeit haben und trotzdem ihre Haut auffrischen und revitalisieren wollen.</p>
      <p class="gap">Reinigung, Enzympeeling, Serum, Maske, Abschlusspflege</p>
      <div class="price"><span>35-45 Min.</span><span>€ 59,00</span></div>
    </article>
    <article class="item" style="top:198px">
      <h3>Classic Facial Treatment – Klassische Gesichtsbehandlung</h3>
      <p>Reinigung, Enzympeeling, Vapozon, Ausreinigung, Augenbrauenkorrektur, Ampulle, Maske, individuelle Abschlusspflege</p>
      <div class="price"><span>45-60 Min.</span><span>€ 89,00</span></div>
    </article>
    <article class="item" style="top:263px">
      <h3>Clear Skin Treatment</h3>
      <p>Die Haut wirkt ausgeglichener, Unreinheiten wird vorgebeugt, der Teint erhält Balance und kann sich beruhigen. Gleichzeitig wird die Haut durch die Hyaluronsäure vitalisiert und Falten und Fältchen kann entgegengewirkt werden.</p>
      <div class="price"><span>50-60 Min.</span><span>€ 89,00</span></div>
    </article>
    <article class="item" style="top:339px">
      <h3>Vasculine Treatment</h3>
      <p>Hautrötungen und Couperose Erscheinungen werden gelindert, die Gefäßwände werden gestärkt und das Hautbild wirkt ausgeglichener, mögliche Irritationen gehen zurück. Gleichzeitig sorgt die hochkonzentrierte Hyaluronsäure für Frische, Vitalität und Glätte.</p>
      <div class="price"><span>50-60 Min.</span><span>€ 89,00</span></div>
    </article>
    <article class="item" style="top:428px">
      <h3>Calmora Soft Treatment (für die empfindliche, gereizte Haut)</h3>
      <p>Entzündliche Prozesse können gemildert werden, gereizte Haut oder solche, die wenig verträgt, wird beruhigt. Irritationen können zurückgehen, die Haut erhält Balance.</p>
      <div class="price"><span>ca. 50 Min.</span><span>€ 79,00</span></div>
    </article>
    <article class="item" style="top:506px">
      <h3>Vitamin Soft Boost</h3>
      <p>Vitamine sorgen für Power und Frische in und auf der Haut, die Widerstandskraft der Haut wird gestärkt. Die Faltentiefe kann gemildert werden.</p>
      <div class="price"><span>ca. 50 Min.</span><span>€ 79,00</span></div>
    </article>
    <article class="item" style="top:584px">
      <h3>Anti-Age Advanced</h3>
      <p>Die Haut wirkt insgesamt erfrischt, vitalisiert und gestrafft. Feine Linien und Fältchen werden reduziert.</p>
      <div class="price" style="gap:30px"><span>50-70 Min. (je nach Peeling)</span><span>€ 99,00</span></div>
    </article>
    <article class="item" style="top:662px">
      <h3>Chemisches Peeling (Oktober – April)</h3>
      <p>Professionelle Peelings können viele Problemstellungen lindern, verbessern oder gar beheben. Dazu gehören die Zellerneuerung, Glättung der Hauttextur, Reduzierung von Pigmentflecken, Verbesserung von Akne</p>
    </article>
  </section>

  <div class="ornament" role="img" aria-label="Dekorative Linienillustration fließender Blattformen in Grau"></div>

  <section class="col-right">
    <article class="item" style="top:126px">
      <h3>AQUAlumi – „Glowing Skin“ Treatment</h3>
      <p>In 6 Schritten zu einer Haut mit einmaligem Glow- Effekt</p>
      <ol class="steps">
        <li>1. Behandlungsschritt: die Haut wird tiefengereinigt</li>
        <li>2. Behandlungsschritt: die obersten Verhornungen und Schuppen werden sanft mit einem Peeling gelöst</li>
        <li>3. Behandlungsschritt: die Haut wird in der Tiefe gereinigt und entschlackt</li>
        <li>4. Behandlungsschritt: niedermolekulare Wirkstoffe werden aufgebracht, um die Haut zu erfrischen und den entsprechenden Glow zu geben</li>
        <li>5. Ausgewählte und hochdosierte Wirkstoffessenzen werden auf die Haut gesprüht und durch die niedrige Molekularstruktur können diese tiefer in der Haut wirken</li>
        <li>6. Zum Schluss werden die Essenzen durch eine Impulsgebende Druckluftmassage noch tiefer in die Haut gebracht</li>
      </ol>
      <div class="price"><span>60 Min.</span><span>€ 140,00</span></div>
    </article>
    <article class="item" style="top:303px">
      <h3>Mikrodermabrasion</h3>
      <p>Bei der Mikrodermabrasion handelt es sich um ein mechanisches Hautpeeling, dabei werden mittels feinster Kristalle die Hornzellen der obersten Hautschicht schonend abgetragen und dann mit Hilfe eines Unterdrucks behutsam abgesaugt. Der revitalisierende Prozess erhöht die Durchblutung, fördert die Zellerneuerung und verleiht ihrer Haut ein zartes frisches Gefühl. Die Haut gewinnt an Spannkraft, feine Fältchen werden gemildert und Poren sichtbar verkleinert. Außerdem hilft es bei oberflächlichen Akne Narben, Pigmentstörungen und Dehnungsstreifen. Wirkstoffe können nun wieder besser von der Haut aufgenommen werden.</p>
      <div class="rates">
        <div class="row"><span>Gesicht</span><span>€ 89,00</span></div>
        <div class="row"><span>Gesicht, Hals, Dekolleté</span><span>€ 110,00</span></div>
      </div>
    </article>
    <article class="item" style="top:458px">
      <h3>Microneedling</h3>
      <p>Die Behandlung eignet sich besonders für Menschen, die ihre Hautqualität verbessern und Falten, (Akne)Narben, Pigmentverschiebungen, große Poren und sogar Haarausfall behandeln wollen. Mit Hilfe feinster Nadeln werden der Haut kontrolliert Mikroverletzungen zugeführt, dies regt die natürliche Wundheilung, sowie Kollagen- und Elastin Bildung an. Microneedling ist also eine natürliche Beauty-Behandlung, die körpereigene Reparaturmechanismen nutzt, um ein strafferes Hautbild zu erhalten. Bereits nach der ersten Behandlung sieht die Haut aufgepolstert, frisch und rosig aus. Kleine Linien und Fältchen werden tiefenbehandelt. Die Haut wirkt straffer und jugendlicher. Ein weiterer Vorteil, durch die Stichkanäle können Wirkstoffe besser von der Haut aufgenommen werden.</p>
      <div class="rates tight" style="margin-top:17px">
        <div class="row"><span>Gesicht</span><span>€ 110,00</span></div>
        <div class="row"><span>Gesicht, Hals</span><span>€ 130,00</span></div>
        <div class="row"><span>Gesicht, Hals, Dekolleté</span><span>€ 150,00</span></div>
      </div>
    </article>
    <article class="item" style="top:655px">
      <h3>Zusatzleistungen</h3>
      <div class="rates tight" style="margin-top:12px">
        <div class="row"><span>Augenbrauen zupfen</span><span>€ 8</span></div>
        <div class="row"><span>Augenbrauen färben</span><span>€ 12</span></div>
        <div class="row"><span>Wimpern färben</span><span>€ 15</span></div>
        <div class="row"><span>Enthaarung störender Gesichtsbehaarung mittels Wax</span><span>€ 10-30</span></div>
      </div>
    </article>
  </section>
</main>
</body>
</html>
```